BOLD & MINIMALIST DESIGN NEEDED

We want a very bold but minimalistic business card design that is impactful and utilizes both sides of the business card. Our current logo is included for your use.

We want bold fonts and good use of negative space. We don't want the logo to overpower the design.

Target Market(s)

Professionals who are building new commercial buildings.

Industry/Entity Type

Construction

Contact Information for Business Card

Name, Title, email, office phone, cell phone, website

Font styles to use
Serif
Sans Serif

Requirements
Must have
• Bold design!

```html
<!DOCTYPE html>
<html lang="en">
<head>
<meta charset="utf-8">
<title>Crestline Business Card</title>
<link rel="stylesheet" href="https://fonts.googleapis.com/css2?family=Arimo:wght@400;700&display=swap">
<style>
  :root {
    --bg: #e6e6e6;
    --paper: #ffffff;
    --ink: #111111;
    --text-gray: #4a4a4a;
    --green: #7cc22e;
    --green-light: #b8e07f;
    --charcoal: #2f2f2f;
    --white: #ffffff;
  }
  * { margin: 0; padding: 0; box-sizing: border-box; }
  html, body {
    width: 1200px; height: 1200px; overflow: hidden;
    background: var(--bg);
    font-family: "Arimo", Arial, sans-serif;
  }
  .canvas { position: relative; width: 1200px; height: 1200px; }
  .card {
    position: absolute; left: 255px; width: 690px; height: 394px;
    box-shadow: 0 18px 30px rgba(0,0,0,0.18);
  }
  .card-front { top: 160px; background: var(--paper); }
  .card-back { top: 652px; background: var(--charcoal); }

  .brand-block {
    position: absolute; left: 0; top: 0; width: 361px; height: 377px;
    display: flex; align-items: center; justify-content: center; gap: 10px;
  }
  .brand-mark { width: 16px; height: 16px; background: var(--green); }
  .brand-name {
    font-weight: 700; font-size: 36px; letter-spacing: 1px; color: var(--ink);
  }
  .divider {
    position: absolute; left: 361px; top: 116px; width: 1px; height: 167px;
    background: linear-gradient(to bottom, transparent, #bdbdbd 20%, #bdbdbd 80%, transparent);
  }
  .person { position: absolute; left: 385px; top: 118px; }
  .person-name { font-weight: 700; font-size: 27px; color: var(--ink); line-height: 1; }
  .person-title { font-size: 15px; color: var(--green); margin-top: 6px; }
  .contact-list { position: absolute; left: 385px; top: 188px; list-style: none; }
  .contact-item {
    display: flex; align-items: center; gap: 12px; height: 21px;
    font-size: 16px; color: var(--text-gray);
  }
  .contact-icon { width: 14px; height: 14px; flex: none; }
  .band { position: absolute; top: 377px; height: 17px; }
  .band-dark { left: 0; width: 419px; background: #0b0b0b; }
  .band-green {
    left: 423px; right: 0;
    background: linear-gradient(to right, var(--green), var(--green-light) 60%, var(--green));
  }

  .back-brand {
    position: absolute; left: 0; right: 0; top: 150px;
    display: flex; align-items: center; justify-content: center; gap: 16px;
  }
  .back-brand .brand-mark { width: 28px; height: 28px; }
  .back-brand .brand-name { font-size: 64px; color: var(--white); letter-spacing: 3px; }
  .back-web {
    position: absolute; left: 0; right: 0; top: 330px; text-align: center;
    font-size: 16px; letter-spacing: 3px; color: var(--white);
  }
  .back-web .accent { color: var(--green); font-weight: 700; }
</style>
</head>
<body>
<div class="canvas">
  <section class="card card-front">
    <div class="brand-block">
      <span class="brand-mark"></span>
      <span class="brand-name">CRESTLINE</span>
    </div>
    <div class="divider"></div>
    <div class="person">
      <div class="person-name">DANIEL REEVES</div>
      <div class="person-title">President</div>
    </div>
    <ul class="contact-list">
      <li class="contact-item">
        <svg class="contact-icon" viewBox="0 0 24 24"><path fill="#111" d="M6.6 10.8a15.5 15.5 0 0 0 6.6 6.6l2.2-2.2c.3-.3.7-.4 1-.2 1.1.4 2.3.6 3.6.6.6 0 1 .4 1 1V20c0 .6-.4 1-1 1C10.6 21 3 13.4 3 4c0-.6.4-1 1-1h3.5c.6 0 1 .4 1 1 0 1.3.2 2.5.6 3.6.1.3 0 .7-.2 1z"/></svg>
        555-210-4187
      </li>
      <li class="contact-item">
        <svg class="contact-icon" viewBox="0 0 24 24"><rect x="6" y="1.5" width="12" height="21" rx="2" fill="none" stroke="#111" stroke-width="2.2"/><rect x="10" y="18" width="4" height="1.6" fill="#111"/></svg>
        555-372-9046
      </li>
      <li class="contact-item">
        <svg class="contact-icon" viewBox="0 0 24 24"><rect x="2" y="5" width="20" height="14" fill="#111"/><path d="M3 6l9 7 9-7" fill="none" stroke="#fff" stroke-width="1.6"/></svg>
        info@crestlinebuild.com
      </li>
      <li class="contact-item">
        <svg class="contact-icon" viewBox="0 0 24 24"><circle cx="12" cy="12" r="10" fill="#111"/><path d="M7 6c2 1 3 3 2 5s1 3 2 5M14 4c0 2 2 3 4 3M15 13c2 0 4 2 3 5" fill="none" stroke="#fff" stroke-width="1.5"/></svg>
        www.crestlinebuild.com
      </li>
    </ul>
    <div class="band band-dark"></div>
    <div class="band band-green"></div>
  </section>

  <section class="card card-back">
    <div class="back-brand">
      <span class="brand-mark"></span>
      <span class="brand-name">CRESTLINE</span>
    </div>
    <div class="back-web">www.<span class="accent">crestlinebuild</span>.com</div>
  </section>
</div>
</body>
</html>
```